Business Card Design Project

I need a Business Card designed using the logo I have also requested be designed via Pixel Harbor. My Business is a consultancy that uses a strength based approach to work with leaders and teams to understand and leverage their strengths to drive business results. I want to communicate that the business is professional and the focus is on performance outcomes for businesses.
Target Market(s)
Business Leaders in western speaking countries
Industry/Entity Type
Business
Font styles to use
Sans Serif
Colors
Designer to choose colors to be used in the design.
Requirements
Must have
- Logo currently being designed by Pixel Harbor + sub-heading of: Strong Teams Achieve Results
name, position title, and contact details
Nice to have
- Norvane Certified Aptitude Guide logo

```html
<!DOCTYPE html>
<html lang="en">
<head>
<meta charset="utf-8">
<title>Business Card – Daniel Rowe</title>
<link rel="stylesheet" href="https://fonts.googleapis.com/css2?family=Noto+Sans:wght@400;700&display=swap">
<style>
  :root {
    --page-bg: #e7e5e1;
    --card-white: #ffffff;
    --card-shade: #f1f1f1;
    --band-slate: #3d4a52;
    --band-highlight: #5c6a73;
    --band-edge: #1f2529;
    --band-text: #ffffff;
    --band-text-soft: #c9d1d6;
    --ink: #2b2b2b;
    --ink-soft: #4a4a4a;
    --mark-grey: #8e9496;
    --mark-text: #8a9092;
  }
  * { margin: 0; padding: 0; box-sizing: border-box; }
  html, body {
    width: 1200px;
    height: 800px;
    overflow: hidden;
    background: var(--page-bg);
  }
  .canvas {
    position: relative;
    width: 1200px;
    height: 800px;
  }
  .card {
    position: absolute;
    left: 150px;
    top: 142px;
    width: 900px;
    height: 515px;
    background: linear-gradient(160deg, var(--card-white) 55%, var(--card-shade) 100%);
    border-radius: 4px;
    box-shadow: 0 14px 34px rgba(0,0,0,0.18);
    overflow: hidden;
    font-family: "Noto Sans", Arial, sans-serif;
    color: var(--ink);
  }
  .card-band {
    position: absolute;
    inset: 0;
    width: 900px;
    height: 515px;
  }
  .brand {
    position: absolute;
    left: 20px;
    bottom: 40px;
    width: 120px;
    color: var(--band-text);
  }
  .brand-square {
    display: block;
    width: 22px;
    height: 22px;
    background: var(--band-text);
    margin-bottom: 10px;
  }
  .brand-name {
    font-size: 17px;
    font-weight: 700;
    line-height: 1.1;
  }
  .brand-tagline {
    margin-top: 8px;
    font-size: 10.5px;
    line-height: 1.4;
    letter-spacing: 1.2px;
    text-transform: uppercase;
    color: var(--band-text-soft);
  }
  .card-content {
    position: absolute;
    left: 300px;
    width: 520px;
    top: 46px;
    text-align: center;
  }
  .cert-mark {
    display: inline-flex;
    align-items: center;
    gap: 14px;
    margin-bottom: 34px;
  }
  .cert-mark-square {
    width: 46px;
    height: 46px;
    background: var(--mark-grey);
  }
  .cert-mark-name {
    font-size: 19px;
    font-weight: 400;
    color: var(--mark-text);
  }
  .person-name {
    font-size: 34px;
    font-weight: 700;
    letter-spacing: -0.5px;
    line-height: 1.1;
  }
  .person-title {
    font-size: 15px;
    color: var(--ink-soft);
    margin-top: 2px;
  }
  .contact-list {
    list-style: none;
    margin-top: 36px;
    font-size: 22px;
    line-height: 1.3;
    color: var(--ink);
    letter-spacing: 0.4px;
  }
  .contact-list .phone { margin-bottom: 6px; }
  .contact-list .address-block { margin-top: 8px; line-height: 1.1; }
</style>
</head>
<body>
<main class="canvas">
  <article class="card">
    <svg class="card-band" viewBox="0 0 900 515" aria-hidden="true">
      <path d="M0,0 H250 C205,60 150,120 150,215 V515 H0 Z" fill="var(--band-slate)"/>
      <path d="M150,0 H250 C232,22 214,44 198,66 L150,66 Z" fill="var(--band-highlight)" opacity="0.55"/>
      <path d="M250,0 C205,60 150,120 150,215 V515" fill="none" stroke="var(--band-edge)" stroke-width="5"/>
    </svg>

    <div class="brand">
      <span class="brand-square"></span>
      <p class="brand-name">Strengthwise</p>
      <p class="brand-tagline">Strong Teams Achieve Results</p>
    </div>

    <div class="card-content">
      <div class="cert-mark">
        <span class="cert-mark-square"></span>
        <span class="cert-mark-name">Norvane Certified Aptitude Guide</span>
      </div>

      <h1 class="person-name">Daniel Rowe</h1>
      <p class="person-title">Project Manager</p>

      <ul class="contact-list">
        <li class="phone">+1 (555) 0134 726</li>
        <li class="phone">+1 (555) 0134 726</li>
        <li class="address-block">48 Harbor Lane, Eastfield,<br>NY 10045</li>
        <li>P.O. Box: 508172</li>
        <li>hello@strengthwise.com</li>
        <li>www.strengthwise.com</li>
      </ul>
    </div>
  </article>
</main>
</body>
</html>
```